Dental Practice Website design

Design a new website for Brambleford Dental Practice.
Design should be warm, neutral in colour, with some small amount of bright colour if needed but kept to a minimum. Website should look professional, high end. Home page should be easy to navigate and simple for patients to be able to book online.
Logo in files along with some examples of websites that we like. Please ask if any further info needed.
Menu should have:
About
New Patients
Treatments
Fees
Contact Us

Industry/Entity Type

Dentistry

Number of Pages Required

4 page

Font styles to use
Sans Serif

Colors

Designer to choose colors to be used in the design.

Requirements
Must have
• Ravelle ratings badge, book online button,
Nice to have
• neutral, relaxing colours
Should not have
• harsh, bright colours!

```html
<!DOCTYPE html>
<html lang="en">
<head>
<meta charset="utf-8">
<title>Brambleford Dental Practice</title>
<link rel="stylesheet" href="https://fonts.googleapis.com/css2?family=Poppins:wght@300;400;500;600;700&family=Montserrat:wght@700&display=swap">
<style>
:root{
  --blue:#1a86c7;
  --ink:#111111;
  --text:#222222;
  --muted:#b9b9b9;
  --sand:#f4f3f1;
  --line:#e6e6e6;
  --hero:#cfcfcf;
  --white:#ffffff;
}
*{box-sizing:border-box;margin:0;padding:0}
html,body{width:1200px;height:3309px;overflow:hidden}
body{position:relative;font-family:"Poppins",sans-serif;color:var(--text);background:var(--white)}
.abs{position:absolute}
.center{left:0;width:1200px;text-align:center}

.topbar{left:0;top:0;width:1200px;height:54px;background:var(--sand)}
.topbar .contact{left:116px;top:16px;font-size:11px;display:flex;gap:12px;align-items:center}
.topbar .contact span{display:flex;align-items:center;gap:7px}
.btn{background:var(--blue);color:var(--white);font-weight:600;text-transform:uppercase;display:flex;align-items:center;justify-content:center;text-decoration:none}
.topbar .btn{left:861px;top:0;width:220px;height:54px;font-size:13px}

.brand{top:86px;font-weight:300;font-size:30px;letter-spacing:2px;color:#333;line-height:1.2}
.brand small{display:block;font-size:18px;letter-spacing:1px}

.nav{left:0;top:210px;width:1200px;height:65px;border-top:1px solid var(--line)}
.nav a{position:absolute;top:24px;font-size:13px;font-weight:500;color:var(--ink);text-decoration:none;transform:translateX(-50%);white-space:nowrap}
.nav a.active{color:var(--blue)}

.hero{left:0;top:275px;width:1200px;height:420px;background:linear-gradient(180deg,#d2d2d2 0%,#c8c8c8 70%,#bdbdbd 100%)}
.hero h1{left:122px;top:92px;font-family:"Montserrat",sans-serif;font-size:62px;color:var(--white);letter-spacing:1px}
.hero p{left:120px;top:168px;width:810px;font-size:11px;line-height:17px;color:var(--ink)}
.hero .btn{left:118px;top:217px;width:188px;height:35px;font-size:13px}

.callband{left:0;top:695px;width:1200px;height:69px;background:var(--blue);color:#cfe6f5;font-size:32px;font-weight:300;text-align:center;line-height:69px}

.eyebrow{font-size:17px;color:var(--ink);text-transform:uppercase}
.title{font-size:46px;font-weight:600;color:var(--ink)}
.title em{font-style:normal;color:var(--blue)}
.sub{font-size:15px;color:var(--ink)}

.booking{left:116px;top:807px;width:962px;height:439px;background:var(--sand);border-radius:26px}
.field{background:var(--white);border-radius:6px;box-shadow:0 2px 6px rgba(0,0,0,.05);font-size:13px;color:#333;padding:20px 24px}
.booking .btn{left:400px;top:386px;width:152px;height:36px;font-size:15px;font-weight:400}

.circle{left:443px;top:1467px;width:326px;height:326px;border-radius:50%;border:6px solid #e8f2fa}
.tooth{left:506px;top:1520px;width:200px;height:225px;border-radius:40% 40% 30% 30%;background:radial-gradient(circle at 40% 30%,#ffffff,#dfe2e6 70%,#c8ccd2)}
.dot{width:9px;height:9px;border-radius:50%;background:var(--blue)}
.feature{width:240px}
.feature h3{font-size:15px;font-weight:500;color:var(--blue);margin-bottom:6px}
.feature p{font-size:12px;line-height:19px;color:var(--ink)}
.feature.left{text-align:right}
.ico{width:40px;height:40px}

.testimonial{left:120px;top:1877px;width:963px;height:420px;background:var(--sand);border-radius:26px}
.quote{font-size:17px;line-height:27px;color:var(--ink)}
.name{font-size:18px;font-weight:600;color:var(--ink)}
.role{font-size:16px;color:var(--muted)}
.dots{display:flex;gap:6px;justify-content:center}
.dots i{width:15px;height:15px;border-radius:50%;background:#cfcfcf;display:block}

.post-img{top:2486px;width:305px;height:172px;border-radius:20px}
.post h3{font-size:15px;font-weight:500;line-height:20px;color:var(--blue)}
.post h3.dark{color:var(--ink);font-weight:400}
.post p{font-size:11.5px;line-height:17px;color:var(--ink);margin-top:10px}
.post{width:290px;top:2670px}

.partner{top:2818px;width:110px;height:40px;border-radius:6px;background:#dcdcdc}

.footer{left:0;top:2918px;width:1200px;height:334px;background:var(--sand)}
.footer h4{font-size:17px;font-weight:600;color:var(--ink);text-transform:uppercase}
.footer ul{list-style:none;font-size:13.5px;line-height:27.5px;color:var(--ink)}
.footer .row{display:flex;align-items:center;gap:14px;font-size:15px;color:var(--ink)}
.social{display:flex;gap:6px}
.social i{display:block;width:30px;height:30px;border-radius:50%;background:var(--ink)}
.hours{left:797px;top:0;width:284px;height:334px;background:var(--blue);color:var(--white);padding:46px 30px}
.hours h4{color:var(--white);margin-bottom:20px}
.hours p{font-size:15px;line-height:33.3px}
.cert{top:260px;width:92px;height:48px;background:#dcdcdc;border-radius:3px}
.ratings{left:445px;top:266px;font-size:28px;font-weight:600;color:var(--blue);line-height:1}
.ratings small{display:block;font-size:12px;margin-top:2px}
.copyright{left:0;top:3252px;width:1200px;height:57px;background:var(--ink);color:var(--white);font-size:11px;font-weight:600;text-align:center;line-height:57px;text-transform:uppercase}
</style>
</head>
<body>

<header class="abs topbar">
  <div class="abs contact">
    <span><svg width="16" height="16" viewBox="0 0 24 24" fill="none" stroke="#222" stroke-width="1.6"><path d="M5 3h4l2 5-3 2a12 12 0 0 0 6 6l2-3 5 2v4a2 2 0 0 1-2 2A18 18 0 0 1 3 5a2 2 0 0 1 2-2z"/></svg>+44 (161) 555-0142</span>
    <span><svg width="18" height="14" viewBox="0 0 24 18" fill="none" stroke="#222" stroke-width="1.6"><rect x="1" y="1" width="22" height="16"/><path d="M1 1l11 9 11-9"/></svg>info@bramblefordental.com</span>
  </div>
  <a class="abs btn" href="#booking">Book an appointment</a>
</header>

<div class="abs center brand">BRAMBLEFORD<small>DENTAL PRACTICE</small></div>

<nav class="abs nav">
  <a class="active" style="left:222px" href="#">HOME</a>
  <a style="left:345px" href="#">ABOUT US</a>
  <a style="left:495px" href="#">NEW PATIENTS</a>
  <a style="left:654px" href="#">TREATMENTS</a>
  <a style="left:790px" href="#">FEES</a>
  <a style="left:928px" href="#">CONTACT US</a>
</nav>

<section class="abs hero" role="img" aria-label="Grey line drawing of the London skyline with bridge, wheel and clock tower">
  <h1 class="abs">Make An Appointment</h1>
  <p class="abs">Lorem Ipsum is simply dummy text of the printing and typesetting industry. Lorem Ipsum has been the industry's standard dummy text ever since the 1500s, when an unknown printer took.</p>
  <a class="abs btn" href="#booking">Book an appointment</a>
</section>

<div class="abs callband">Get in touch with us today +44 (161) 555-0142</div>

<section class="abs booking" id="booking">
  <div class="abs eyebrow" style="left:0;width:962px;text-align:center;top:26px">Booking</div>
  <div class="abs title" style="left:0;width:962px;text-align:center;top:44px"><em>Make An</em> Appointment</div>
  <div class="abs field" style="left:127px;top:121px;width:344px;height:53px">First Name</div>
  <div class="abs field" style="left:492px;top:121px;width:344px;height:53px">Email</div>
  <div class="abs field" style="left:127px;top:185px;width:344px;height:53px">Phone Number</div>
  <div class="abs field" style="left:492px;top:185px;width:344px;height:53px">Date</div>
  <div class="abs field" style="left:127px;top:246px;width:709px;height:122px">Message</div>
  <a class="abs btn" href="#">Send Message</a>
</section>

<div class="abs center eyebrow" style="top:1298px">Why choose us</div>
<div class="abs center title" style="top:1325px"><em>Diagnosis</em> Dental Diseases</div>
<div class="abs center sub" style="top:1394px">Lorem Ipsum is simply dummy text of the printing.</div>

<div class="abs circle"></div>
<div class="abs tooth" role="img" aria-label="Glossy white molar tooth"></div>
<i class="abs dot" style="left:472px;top:1526px"></i>
<i class="abs dot" style="left:727px;top:1526px"></i>
<i class="abs dot" style="left:438px;top:1626px"></i>
<i class="abs dot" style="left:761px;top:1626px"></i>
<i class="abs dot" style="left:481px;top:1737px"></i>
<i class="abs dot" style="left:718px;top:1737px"></i>

<div class="abs feature left" style="left:118px;top:1484px"><h3>Experienced Doctor</h3><p>Lorem Ipsum is simply dummy text of the printing and typesetting industry.</p></div>
<div class="abs feature left" style="left:118px;top:1600px"><h3>Personalized Care</h3><p>Lorem Ipsum is simply dummy text of the printing and typesetting industry.</p></div>
<div class="abs feature left" style="left:118px;top:1709px"><h3>Flexible Payment Options</h3><p>Lorem Ipsum is simply dummy text of the printing and typesetting industry.</p></div>
<div class="abs feature" style="left:836px;top:1484px"><h3>Emergency Services</h3><p>Lorem Ipsum is simply dummy text of the printing and typesetting industry.</p></div>
<div class="abs feature" style="left:836px;top:1600px"><h3>Positive Patient Reviews</h3><p>Lorem Ipsum is simply dummy text of the printing and typesetting industry.</p></div>
<div class="abs feature" style="left:836px;top:1709px"><h3>Latest Technology</h3><p>Lorem Ipsum is simply dummy text of the printing and typesetting industry.</p></div>

<svg class="abs ico" style="left:378px;top:1510px" viewBox="0 0 40 40" fill="none" stroke="#1a86c7" stroke-width="1.5"><circle cx="16" cy="16" r="6"/><path d="M4 36c0-8 5-12 12-12s12 4 12 12z"/><rect x="24" y="4" width="12" height="14"/></svg>
<svg class="abs ico" style="left:373px;top:1618px" viewBox="0 0 40 40" fill="none" stroke="#1a86c7" stroke-width="1.5"><path d="M10 8c4-3 8 0 10 0s6-3 10 0c3 3 1 10-1 14l-2 12c-1 2-3 1-3-1l-2-8h-4l-2 8c0 2-2 3-3 1l-2-12C9 18 7 11 10 8z"/></svg>
<svg class="abs ico" style="left:378px;top:1728px" viewBox="0 0 40 40" fill="none" stroke="#1a86c7" stroke-width="1.5"><circle cx="22" cy="12" r="8"/><path d="M4 30h8l8 4 14-6-2-3-12 3"/></svg>
<svg class="abs ico" style="left:786px;top:1500px" viewBox="0 0 40 40" fill="none" stroke="#1a86c7" stroke-width="1.5"><path d="M8 6h6l3 7-4 3a16 16 0 0 0 9 9l3-4 7 3v6c0 2-1 3-3 3C17 33 6 22 6 9c0-2 1-3 2-3z"/><circle cx="26" cy="12" r="7"/><path d="M26 8v8M22 12h8"/></svg>
<svg class="abs ico" style="left:786px;top:1612px" viewBox="0 0 40 40" fill="none" stroke="#1a86c7" stroke-width="1.5"><rect x="2" y="4" width="36" height="10"/><circle cx="10" cy="24" r="4"/><path d="M3 36c0-5 3-7 7-7s7 2 7 7"/><path d="M22 22h14M22 27h14M22 32h14"/></svg>
<svg class="abs ico" style="left:786px;top:1722px" viewBox="0 0 40 40" fill="none" stroke="#1a86c7" stroke-width="1.5"><circle cx="16" cy="24" r="9"/><circle cx="16" cy="24" r="4"/><circle cx="31" cy="9" r="5"/></svg>

<section class="abs testimonial">
  <div class="abs eyebrow" style="left:0;width:963px;text-align:center;top:65px">Testimonial</div>
  <div class="abs title" style="left:0;width:963px;text-align:center;top:96px"><em>What Our</em> Clients Say</div>
  <div class="abs quote" style="left:0;width:963px;text-align:center;top:170px">“ The choice of profession is very important. I made my choice. And I have never regretted about it.<br>I’m glad that my job is to help people to become a little healthier and<br>more beautiful “Dentist –<br>similar to parents, but they criticise yoour teeth instead of your lifestyle. ”</div>
  <div class="abs name" style="left:0;width:963px;text-align:center;top:302px">Daniel Hartley</div>
  <div class="abs role" style="left:0;width:963px;text-align:center;top:327px">Dental Implants</div>
  <div class="abs dots" style="left:0;width:963px;top:370px"><i></i><i></i><i></i></div>
</section>

<div class="abs center eyebrow" style="top:2341px">Blogs</div>
<div class="abs center title" style="top:2366px"><em>Check Our</em> Latest Articles</div>
<div class="abs center sub" style="top:2431px">Lorem Ipsum is simply dummy text of the printing.</div>

<div class="abs post-img" style="left:116px;background:linear-gradient(135deg,#d8c5b6,#5e9ab0)" role="img" aria-label="Smiling patient during a dental check-up"></div>
<div class="abs post-img" style="left:446px;background:linear-gradient(135deg,#8fb3cf,#3f7d9a)" role="img" aria-label="Dentist treating a patient in the chair"></div>
<div class="abs post-img" style="left:774px;background:linear-gradient(135deg,#b4cde0,#5c93b4)" role="img" aria-label="Smiling patient with dentist's instruments"></div>

<article class="abs post" style="left:130px"><h3 class="dark">The Importance of Regular Dental Check-Ups</h3><p>Lorem Ipsum is simply dummy text of the printing and typesetting industry.</p></article>
<article class="abs post" style="left:459px"><h3>Top 5 Benefits of Professional Teeth Whitening</h3><p>Lorem Ipsum is simply dummy text of the printing and typesetting industry.</p></article>
<article class="abs post" style="left:783px"><h3>Understanding Dental Implants: What You Need to Know</h3><p>Lorem Ipsum is simply dummy text of the printing and typesetting industry.</p></article>

<div class="abs partner" style="left:130px"></div>
<div class="abs partner" style="left:292px"></div>
<div class="abs partner" style="left:470px"></div>
<div class="abs partner" style="left:636px"></div>
<div class="abs partner" style="left:825px"></div>
<div class="abs partner" style="left:960px"></div>

<footer class="abs footer">
  <h4 class="abs" style="left:119px;top:44px">Quick Links</h4>
  <ul class="abs" style="left:119px;top:84px"><li>About</li><li>New Patients</li><li>Treatments</li><li>Fees</li><li>Contact Us</li></ul>
  <h4 class="abs" style="left:293px;top:44px">Dental Departments</h4>
  <ul class="abs" style="left:293px;top:84px"><li>Cosmetic Dentistry</li><li>Endodontics</li><li>Oral Surgery</li><li>General Dental Care</li><li>Pediatric Dentistry</li></ul>
  <h4 class="abs" style="left:538px;top:44px">Contact Us</h4>
  <div class="abs row" style="left:538px;top:86px"><svg width="20" height="20" viewBox="0 0 24 24" fill="none" stroke="#222" stroke-width="1.5"><path d="M5 3h4l2 5-3 2a12 12 0 0 0 6 6l2-3 5 2v4a2 2 0 0 1-2 2A18 18 0 0 1 3 5a2 2 0 0 1 2-2z"/></svg>+44 (161) 555-0142</div>
  <div class="abs row" style="left:538px;top:124px"><svg width="22" height="16" viewBox="0 0 24 18" fill="none" stroke="#222" stroke-width="1.5"><rect x="1" y="1" width="22" height="16"/><path d="M1 1l11 9 11-9"/></svg>info@bramblefordental.com</div>
  <div class="abs row" style="left:538px;top:158px;font-size:13px"><svg width="20" height="22" viewBox="0 0 24 26" fill="none" stroke="#222" stroke-width="1.5"><path d="M12 25s-8-9-8-15a8 8 0 0 1 16 0c0 6-8 15-8 15z"/><circle cx="12" cy="10" r="3"/></svg>12 Orchard Lane, UK</div>
  <div class="abs row" style="left:538px;top:216px;font-size:13px">Follow me: <span class="social"><i></i><i></i><i></i><i></i></span></div>
  <div class="abs cert" style="left:119px"></div>
  <div class="abs cert" style="left:224px"></div>
  <div class="abs cert" style="left:331px"></div>
  <div class="abs ratings">Ravelle<small>Ratings ★★★★★</small></div>
  <div class="abs hours">
    <h4>Opening Hours</h4>
    <p>Monday : 08.00 - 10.00</p>
    <p>Tuesday : 08.00 - 10.00</p>
    <p>Wednesday : 08.00 - 10.00</p>
    <p>Thursday : 08.00 - 10.00</p>
    <p>Friday : 09.00 - 07.00</p>
    <p>Saturday : 10.00 - 05.00</p>
    <p>Sunday : 10.00 - 05.00</p>
  </div>
</footer>

<div class="abs copyright">Copyright © 2025 Brambleford Dental Practice. All rights reserved.</div>

</body>
</html>
```